biopharma company with breakthrough technology needs new web design

The rise of multidrug resistant bacteria pose a worldwide healthcare crisis as new bacterial strains are now resistant to nearly all existing antibiotics. Q4 Biotic is developing a class of new compounds known as ceragenins that have broad spectrum activity against even resistant strains. Our website needs a facelift. See www.q4biotic.com. We want to provide more information on the landing page and make it more visually appealing. see for example: http://vorelaxin.com/#sthash.KmpwRtaZ.qxle
Industry/Entity Type
Healthcare

```html
<!DOCTYPE html>
<html lang="en">
<head>
<meta charset="utf-8">
<title>Q4 Biotic</title>
<link href="https://fonts.googleapis.com/css2?family=Questrial&family=Arimo:wght@400;700&family=Open+Sans:wght@400;700&display=swap" rel="stylesheet">
<style>
:root{
  --navy:#0c2461;
  --navy-band:#163a82;
  --cyan:#13b7f0;
  --grey-text:#8a8a8a;
  --dark-text:#333333;
  --panel:#efefef;
  --field:#eeeeee;
  --white:#ffffff;
}
*{margin:0;padding:0;box-sizing:border-box}
html,body{width:1200px;height:2671px;overflow:hidden;background:var(--white)}
body{position:relative;font-family:"Arimo",Arial,sans-serif;color:var(--dark-text)}
.abs{position:absolute}
.display{font-family:"Questrial","Century Gothic",sans-serif}
.accent{color:var(--cyan)}

/* hero */
.hero{left:0;top:0;width:1200px;height:605px;
  background:linear-gradient(100deg,#e9eef3 0%,#f4f6f8 30%,#dfe6ee 60%,#c9d3dd 100%)}
.hero-call{left:880px;top:30px;display:flex;align-items:center;gap:12px;color:var(--navy)}
.hero-call small{display:block;font-size:16px;color:#fff;text-shadow:0 0 3px rgba(0,0,0,.25)}
.hero-call b{display:block;font-size:26px;font-weight:400;color:var(--navy)}
.brand-mark{left:0;width:1200px;top:250px;text-align:center;font-family:"Questrial",sans-serif;
  font-size:120px;line-height:1;color:var(--navy)}

/* nav */
.nav{left:0;top:605px;width:1200px;height:63px;background:rgba(255,255,255,.85);border-top:2px solid var(--navy)}
.nav-base{left:0;top:666px;width:1200px;height:11px;background:var(--navy)}
.nav-pointer{left:586px;top:676px}
.nav-shadow{left:40px;top:677px;width:1120px;height:60px;
  background:radial-gradient(ellipse at 50% 0%,rgba(0,0,0,.18),rgba(0,0,0,0) 70%)}
.nav-item{top:605px;height:61px;line-height:64px;font-size:17px;color:#222;text-align:center}
.nav-item.active{background:var(--cyan);color:#fff}

/* welcome */
.section-title{left:0;width:1200px;text-align:center;font-size:41px;color:var(--navy);letter-spacing:1px}
.welcome-lead{left:0;width:1200px;top:818px;text-align:center;font-size:16px;color:#333}
.welcome-body{left:151px;width:900px;top:854px;text-align:center;font-size:14.5px;line-height:27px;color:var(--grey-text)}
.btn{display:block;background:var(--navy);color:#fff;font-family:"Questrial",sans-serif;font-size:19px;text-align:center}
.welcome-btn{left:517px;top:944px;width:165px;height:62px;line-height:62px}

/* features */
.features{left:0;top:1069px;width:1200px;height:422px;background:var(--panel)}
.features-art{left:0;top:1069px;width:1200px;height:422px;
  background:radial-gradient(circle at 330px 200px,rgba(200,200,200,.35),transparent 260px),
             radial-gradient(circle at 960px 260px,rgba(210,200,190,.35),transparent 260px)}
.features-divider{left:582px;top:1069px;width:4px;height:422px;background:linear-gradient(to right,rgba(0,0,0,.06),rgba(255,255,255,.8))}
.feature{width:480px}
.feature h2{font-family:"Questrial",sans-serif;font-weight:400;font-size:35px;color:var(--navy);line-height:1}
.feature h3{font-weight:400;font-size:18px;color:var(--navy);margin-top:20px}
.feature p{font-size:14.5px;line-height:27px;color:var(--grey-text);margin-top:12px;height:112px}
.feature .btn{width:167px;height:62px;line-height:62px;margin-top:20px}

/* news */
.news{width:340px;height:130px}
.news-date{left:0;top:0;width:90px;height:107px}
.news-day{height:57px;background:var(--cyan);color:#fff;font-family:"Questrial",sans-serif;font-size:36px;text-align:center;line-height:58px}
.news-month{height:50px;background:var(--navy);color:#fff;font-size:18px;text-align:center;line-height:50px}
.news-title{left:103px;top:0;font-family:"Questrial",sans-serif;font-variant:small-caps;font-size:20px;color:var(--navy)}
.news-text{left:105px;top:28px;width:240px;font-size:14.5px;line-height:23px;color:#555}
.news-more{left:107px;top:100px;font-family:"Questrial",sans-serif;font-size:16px;color:var(--cyan)}

/* contact */
.contact{left:0;top:1826px;width:1200px;height:543px;background:var(--navy-band)}
.contact-art{left:0;top:1826px;width:1200px;height:543px;
  background:radial-gradient(circle at 800px 150px,rgba(255,255,255,.07),transparent 300px),
             radial-gradient(circle at 1100px 480px,rgba(255,255,255,.05),transparent 200px)}
.contact-title{color:#fff}
.form-label{left:114px;top:1978px;width:616px;display:flex;align-items:center;gap:10px;
  font-family:"Questrial",sans-serif;font-variant:small-caps;font-size:26px;color:var(--cyan);white-space:nowrap}
.form-label::before,.form-label::after{content:"";flex:1;height:2px;background:var(--cyan)}
.info-label{left:851px;top:1975px;width:211px;text-align:center;font-family:"Questrial",sans-serif;font-size:25px;color:var(--cyan)}
.field{background:var(--field);border:2px solid var(--cyan);font-size:14px;color:#555;padding:14px 12px}
.send{left:128px;top:2201px}
.globe{left:853px;top:2016px;width:206px;height:206px;border-radius:50%;
  background:radial-gradient(circle at 45% 40%,#33c4f4,#0a8fd0 70%);border:3px solid var(--cyan)}
.info-card{left:851px;top:2151px;width:217px;height:146px;background:rgba(90,130,190,.55);border:1px solid rgba(150,200,240,.6);
  font-family:"Open Sans",sans-serif;color:#fff;text-align:center;font-size:15px;line-height:23px;padding-top:12px}
.info-card strong{font-size:18px;display:block;margin-bottom:2px}
.pin{left:890px;top:2036px}

/* footer */
.footer-brand{left:0;width:1200px;top:2400px;text-align:center;font-family:"Questrial",sans-serif;font-size:52px;line-height:1;color:var(--navy)}
.copyright{left:0;width:1200px;top:2503px;text-align:center;font-size:15px;color:#555}
.social{top:2539px;width:54px;height:54px;border-radius:50%;border:4px solid #d6d6d6}
.social.primary{background:var(--navy)}
.social.muted{background:#9a9a9a}
.bottom-bar{left:0;top:2648px;width:1200px;height:23px;background:var(--navy);border-top:4px solid var(--cyan)}
.bottom-pointer{left:585px;top:2630px}
</style>
</head>
<body>

<div class="abs hero" role="img" aria-label="Photo of a scientist in safety glasses examining a flask of yellow liquid in a laboratory"></div>
<div class="abs hero-call">
  <svg width="40" height="40" viewBox="0 0 24 24" aria-hidden="true"><path fill="#0c2461" d="M6.6 10.8a15.2 15.2 0 0 0 6.6 6.6l2.2-2.2a1 1 0 0 1 1-.25 11.4 11.4 0 0 0 3.6.57 1 1 0 0 1 1 1V20a1 1 0 0 1-1 1A17 17 0 0 1 3 4a1 1 0 0 1 1-1h3.5a1 1 0 0 1 1 1c0 1.25.2 2.45.57 3.57a1 1 0 0 1-.25 1z"/></svg>
  <div><small>Call Us Know</small><b>555 - 214 - 7060</b></div>
</div>
<div class="abs brand-mark">Q4 Biotic</div>

<div class="abs nav-shadow"></div>
<nav>
  <div class="abs nav"></div>
  <div class="abs nav-base"></div>
  <svg class="abs nav-pointer" width="28" height="14" aria-hidden="true"><path d="M0 0h28L14 14z" fill="#0c2461"/></svg>
  <a class="abs nav-item active" style="left:194px;width:103px">HOME</a>
  <a class="abs nav-item" style="left:334px;width:80px">ABOUT</a>
  <a class="abs nav-item" style="left:446px;width:140px">TECHNOLOGY</a>
  <a class="abs nav-item" style="left:616px;width:160px">MEDICAL DEVICE</a>
  <a class="abs nav-item" style="left:814px;width:100px">CONTACT</a>
  <a class="abs nav-item" style="left:941px;width:80px">NEWS</a>
</nav>

<h1 class="abs section-title display" style="top:756px;font-weight:400">WELCOME TO <span class="accent">Q4 BIOTIC</span></h1>
<p class="abs welcome-lead">Fortifying Medical Devices with Their Own Immune Systems to Prevent Hospital- Acqu - ired Infections.</p>
<p class="abs welcome-body">Q4 Biotic is a development-stage medical device company focused upon commercializing antimicrobial medical devices and coatings to address the multibillion dollar public health and economic burden associated with medical device-related hospital acquired infections (“HAIs”). Q4 Biotic’s business is based on the application of a novel.</p>
<a class="abs btn welcome-btn">READ MORE</a>

<div class="abs features"></div>
<div class="abs features-art" role="img" aria-label="Faint molecular model and capsule imagery in the background"></div>
<div class="abs features-divider"></div>
<section class="abs feature" style="left:78px;top:1132px">
  <h2>OUR <span class="accent">TECHNOLOGY</span></h2>
  <h3>Ceragenin Technology</h3>
  <p>Ceragenins, also known as cationic steroidal antimicrobials or CSAs, are synthetic, non-peptide small molecule mimetics of endogenous host defense or antimicrobial peptides. Ceragenins have broad-spectrum activity mimicking those of endogenous host defense peptides. However, Ceragenins, are not peptides.</p>
  <a class="btn">READ MORE</a>
</section>
<section class="abs feature" style="left:634px;top:1132px">
  <h2>MEDICA <span class="accent">DEVICE</span></h2>
  <h3>The hai problem</h3>
  <p>nfections are a leading cause of death and illness worldwide. With the rapid rise of drug-resistant bacteria, nearly 70 percent of infections in the U.S. are now drug resistant, making the problem one of the most serious in the medical field. Hospital-acquired infections and healthcare-associated infections (HAIs) are a large.</p>
  <a class="btn">READ MORE</a>
</section>

<h2 class="abs section-title display" style="top:1552px;font-weight:400">LATEST <span class="accent">NEWS</span></h2>

<article class="abs news" style="left:77px;top:1638px">
  <div class="abs news-date"><div class="news-day">05</div><div class="news-month">June</div></div>
  <div class="abs news-title">Medical Device</div>
  <p class="abs news-text">Q4 Biotic, an emerging pharma - ceutical company addressing life -threatening global..</p>
  <a class="abs news-more">READ MORE... »</a>
</article>
<article class="abs news" style="left:431px;top:1638px">
  <div class="abs news-date"><div class="news-day">05</div><div class="news-month">June</div></div>
  <div class="abs news-title">Medical Device</div>
  <p class="abs news-text">Q4 Biotic, an emerging pharma - ceutical company addressing life -threatening global..</p>
  <a class="abs news-more">READ MORE... »</a>
</article>
<article class="abs news" style="left:785px;top:1638px">
  <div class="abs news-date"><div class="news-day">05</div><div class="news-month">June</div></div>
  <div class="abs news-title">Medical Device</div>
  <p class="abs news-text">Q4 Biotic, an emerging pharma - ceutical company addressing life -threatening global..</p>
  <a class="abs news-more">READ MORE... »</a>
</article>

<div class="abs contact"></div>
<div class="abs contact-art" role="img" aria-label="Faint molecule diagram and laboratory photo behind the contact area"></div>
<h2 class="abs section-title display contact-title" style="top:1886px;font-weight:400">CONTACT <span class="accent">US</span></h2>
<div class="abs form-label">Send Us a Message</div>
<div class="abs info-label">CONTACT INFO</div>

<div class="abs field" style="left:77px;top:2045px;width:219px;height:50px">Name</div>
<div class="abs field" style="left:317px;top:2045px;width:217px;height:50px">E-Mail</div>
<div class="abs field" style="left:556px;top:2045px;width:219px;height:50px">Subject</div>
<div class="abs field" style="left:77px;top:2107px;width:698px;height:144px">Message</div>
<svg class="abs send" width="106" height="106" viewBox="0 0 106 106" aria-label="Send">
  <circle cx="53" cy="53" r="52" fill="#1b8fd6"/>
  <circle cx="53" cy="53" r="40" fill="#0a2a66" stroke="#5ec9f5" stroke-width="3"/>
  <rect x="38" y="42" width="30" height="21" rx="2" fill="#9fd3f2"/>
  <path d="M38 43l15 11 15-11" fill="none" stroke="#2a6fb0" stroke-width="2"/>
</svg>

<div class="abs globe" role="img" aria-label="Globe map showing the company location"></div>
<svg class="abs pin" width="34" height="46" viewBox="0 0 24 32" aria-hidden="true"><path d="M12 0a10 10 0 0 0-10 10c0 8 10 22 10 22s10-14 10-22A10 10 0 0 0 12 0z" fill="#e8456b"/><circle cx="12" cy="10" r="4" fill="#fff"/></svg>
<address class="abs info-card" style="font-style:normal">
  <strong>Q4 BIOTIC</strong>
  412 Alder Ln Marlow,<br>OH 45099<br>Phone : 555 - 214 - 7060<br>Fax : 555 - 214 - 7061
</address>

<footer>
  <div class="abs footer-brand">Q4 Biotic</div>
  <p class="abs copyright"><span class="accent">©Q4 BIOTIC, Inc.</span> 2016 All rights reserved.</p>
  <span class="abs social primary" style="left:465px" aria-label="Social link"></span>
  <span class="abs social muted" style="left:538px" aria-label="Social link"></span>
  <span class="abs social muted" style="left:611px" aria-label="Social link"></span>
  <span class="abs social muted" style="left:684px" aria-label="Social link"></span>
  <svg class="abs bottom-pointer" width="30" height="18" aria-hidden="true"><path d="M0 18L15 0l15 18z" fill="#13b7f0"/></svg>
  <div class="abs bottom-bar"></div>
</footer>

</body>
</html>
```